Sell the dream! Property investment proposal document

We are looking for a proposal document which outlines our vision for property development. The purpose of the document is to raise investment from investors - sell the dream!
Brief summary:
Kestrel Dwellings Developments, is an emerging New Zealand property investment company with a focus on providing unique property investment opportunities.
Our expertise and capabilities in architectural modular homes provide us with a remarkable advantage in tackling the development of properties that are typically considered challenging, remote, or uniquely positioned.
Our specialization in this niche sector of property development not only sets us apart from competitors, but also paves the way for lucrative investment opportunities in the New Zealand property market.
Feel free to use any images from www.kestreldwellings.co.nz
Target Market(s)
investors for a unique property development opportunity
Industry/Entity Type
luxury property development in unique locations throughout New Zealand
Colors
Designer to choose only greyscale colors for use in the design.
Look and feel

```html
<!DOCTYPE html>
<html lang="en">
<head>
<meta charset="utf-8">
<title>Kestrel Dwellings Developments – Investment Proposal</title>
<link href="https://fonts.googleapis.com/css2?family=Manrope:wght@300;400;600;700&display=swap" rel="stylesheet">
<style>
  :root {
    --paper: #ffffff;
    --page: #2e2c2c;
    --ink: #f2f2f2;
    --ink-soft: #d9d9d9;
    --rule: #6a6767;
    --rule-light: #8c8989;
  }
  * { margin: 0; padding: 0; box-sizing: border-box; }
  html, body { width: 1200px; height: 529px; overflow: hidden; background: var(--paper); }
  body { position: relative; font-family: "Manrope", sans-serif; color: var(--ink); }

  .page { position: absolute; background: var(--page); overflow: hidden; }
  .page--cover { left: 16px; top: 14px; width: 383px; height: 494px; }
  .page--contents { left: 404px; top: 14px; width: 383px; height: 494px; }
  .page--overview { left: 792px; top: 16px; width: 383px; height: 495px; }

  .photo { position: absolute; }

  /* Cover */
  .cover__photo {
    left: 143px; top: 0; width: 240px; height: 280px;
    background: linear-gradient(180deg, #e9eef2 0%, #d3dbe0 38%, #4c4d4a 55%, #5f6f3e 72%, #6f9a3a 100%);
  }
  .cover__frame { position: absolute; border: 0.6px solid var(--rule-light); border-right: none; border-top: none; }
  .cover__frame--a { left: 130px; top: 0; width: 13px; height: 266px; }
  .cover__frame--b { left: 136px; top: 0; width: 7px; height: 275px; }
  .cover__corner { position: absolute; left: 365px; top: 280px; width: 18px; height: 12px; border-left: 0.6px solid var(--rule-light); border-bottom: 0.6px solid var(--rule-light); }
  .cover__brand {
    position: absolute; left: 28px; top: 24px; height: 256px; width: 80px;
    writing-mode: vertical-rl; transform: rotate(180deg);
    font-size: 60px; font-weight: 400; letter-spacing: 1px; line-height: 80px;
    text-align: center; color: var(--ink);
  }
  .cover__tagline { position: absolute; left: 0; top: 352px; width: 383px; text-align: center; font-size: 34px; line-height: 44px; letter-spacing: 0.5px; }
  .cover__tagline-light { display: block; font-weight: 300; }
  .cover__tagline-bold { display: block; font-weight: 700; }

  /* Contents */
  .contents__photo {
    left: 0; top: 0; width: 383px; height: 191px;
    background: linear-gradient(180deg, #bfb8a8 0%, #8d8678 30%, #5a5a3c 55%, #4a4b2a 80%, #3b3825 100%);
  }
  .contents__corner { position: absolute; width: 28px; height: 18px; border-bottom: 0.6px solid var(--rule-light); }
  .contents__corner--left { left: 0; top: 191px; border-right: 0.6px solid var(--rule-light); }
  .contents__corner--right { right: 0; top: 191px; border-left: 0.6px solid var(--rule-light); }
  .contents__title {
    position: absolute; left: 28px; top: 226px; height: 236px; width: 26px;
    writing-mode: vertical-rl; transform: rotate(180deg);
    font-size: 22px; line-height: 26px; letter-spacing: 0.3px; white-space: nowrap;
  }
  .contents__title-light { font-weight: 300; }
  .contents__title-bold { font-weight: 700; }
  .contents__list { position: absolute; left: 86px; top: 222px; width: 279px; list-style: none; }
  .contents__item {
    display: flex; justify-content: space-between; align-items: center;
    height: 36.8px; font-size: 13px; font-weight: 400; letter-spacing: 0.2px;
    border-bottom: 0.6px solid var(--rule);
  }
  .contents__item:last-child { border-bottom: none; }

  /* Overview */
  .overview__header { position: absolute; left: 18px; top: 20px; width: 347px; display: flex; align-items: center; gap: 8px; }
  .overview__rule { flex: 1; height: 0; border-top: 0.6px solid var(--rule-light); }
  .overview__brand { font-size: 10.5px; font-weight: 400; }
  .overview__heading { position: absolute; left: 18px; top: 44px; font-size: 16px; font-weight: 400; letter-spacing: 0.2px; }
  .overview__body { position: absolute; left: 18px; top: 80px; width: 347px; font-size: 6.6px; line-height: 11.2px; color: var(--ink-soft); }
  .overview__body p { margin-bottom: 7px; text-align: justify; }
  .overview__photo {
    left: 0; top: 303px; width: 383px; height: 166px;
    background: linear-gradient(180deg, #d6dde3 0%, #9aa7b1 25%, #6f7e5a 50%, #8c9a5c 68%, #a89682 85%, #7b6650 100%);
  }
  .overview__corner { position: absolute; left: 0; top: 469px; width: 27px; height: 16px; border-right: 0.6px solid var(--rule-light); border-bottom: 0.6px solid var(--rule-light); }
  .overview__folio { position: absolute; right: 18px; top: 474px; font-size: 8px; }
</style>
</head>
<body>

<section class="page page--cover">
  <div class="photo cover__photo" role="img" aria-label="Dark modern cantilevered house on a grassy rock outcrop above the sea"></div>
  <div class="cover__frame cover__frame--a"></div>
  <div class="cover__frame cover__frame--b"></div>
  <div class="cover__corner"></div>
  <div class="cover__brand">Kestrel</div>
  <h1 class="cover__tagline">
    <span class="cover__tagline-light">A NEST TO MAKE</span>
    <span class="cover__tagline-bold">YOUR OWN</span>
  </h1>
</section>

<section class="page page--contents">
  <div class="photo contents__photo" role="img" aria-label="Low dark timber house on rolling green farmland beside the ocean at dusk"></div>
  <div class="contents__corner contents__corner--left"></div>
  <div class="contents__corner contents__corner--right"></div>
  <h2 class="contents__title"><span class="contents__title-light">TABLE OF </span><span class="contents__title-bold">CONTENT</span></h2>
  <ol class="contents__list">
    <li class="contents__item"><span>BUSINESS OVERVIEW</span><span>X</span></li>
    <li class="contents__item"><span>BUSINESS ORIGINS</span><span>X</span></li>
    <li class="contents__item"><span>COMPETITIVE ADVANTAGE</span><span>X</span></li>
    <li class="contents__item"><span>FINANCIAL SUMMARY</span><span>X</span></li>
    <li class="contents__item"><span>OUR MISSION</span><span>X</span></li>
    <li class="contents__item"><span>ARCHITECHTURAL DESIGN</span><span>X</span></li>
    <li class="contents__item"><span>CONCLUSION</span><span>X</span></li>
  </ol>
</section>

<section class="page page--overview">
  <header class="overview__header">
    <span class="overview__rule"></span>
    <span class="overview__brand">Kestrel</span>
  </header>
  <h2 class="overview__heading">1. BUSINESS OVERVIEW</h2>
  <div class="overview__body">
    <p>Kestrel Dwellings Developments, is an emerging New Zealand property investment company with a focus on providing unique property investment opportunities.</p>
    <p>Our expertise and capabilities in architectural modular homes provide us with a remarkable advantage in tackling the development of properties that are typically considered challenging, remote, or uniquely positioned.</p>
    <p>As a company, with 48 employees boasting a wealth of experience in handling complex architectural projects, making us well-equipped to navigate the intricacies and demands of such ventures.</p>
    <p>This advantage allows us to not only execute projects efficiently but also to deliver exceptional results within condensed time frames.</p>
    <p>By capitalizing on our ability to develop difficult, remote, or one-of-a-kind properties swiftly and effectively, Kestrel Dwellings Developments offers investors a rare chance to engage in projects that promise exceptional profitability in the New Zealand property market.</p>
    <p>Our specialization in this niche sector of property development not only sets us apart from competitors, but also paves the way for lucrative investment opportunities in the New Zealand property market.</p>
  </div>
  <div class="photo overview__photo" role="img" aria-label="Interior with floor-to-ceiling glass looking over green hills and a harbour, timber floor and lounge seating"></div>
  <div class="overview__corner"></div>
  <span class="overview__folio">1</span>
</section>

</body>
</html>
```